Business Card For Halvenmoor Financial Consulting

Hi, I would like a business card designed. Bold, modern.
Please use the same design as the logo. I have also attached the website design to see the overall theme.
Wordmark Font
Color: Hex: #01AEF7

```html
<!DOCTYPE html>
<html lang="en">
<head>
<meta charset="utf-8">
<title>Halvenmoor Financial Consulting – Business Card</title>
<link href="https://fonts.googleapis.com/css2?family=Source+Sans+3:wght@400;700&display=swap" rel="stylesheet">
<style>
  :root {
    --backdrop: #e6e6e6;
    --card-dark: #13212b;
    --card-dark-deep: #0d1820;
    --brand-blue: #35a2d8;
    --text-light: #ffffff;
    --text-soft: #e8edf1;
  }
  * { margin: 0; padding: 0; box-sizing: border-box; }
  html, body {
    width: 1200px; height: 960px; overflow: hidden;
    background: var(--backdrop);
    font-family: "Source Sans 3", "Source Sans Pro", Arial, sans-serif;
  }
  .canvas { position: relative; width: 1200px; height: 960px; }
  .card {
    position: absolute; left: 296px; width: 610px; height: 348px;
    background: var(--card-dark); overflow: hidden;
  }
  .card--front { top: 109px; }
  .card--back { top: 510px; }

  .front-pattern {
    position: absolute; inset: 0;
    background: linear-gradient(90deg, #2a3944 0%, #18262f 45%, var(--card-dark-deep) 100%);
  }
  .wordmark {
    position: absolute; display: flex; align-items: center; gap: 14px;
  }
  .wordmark__square {
    display: block; background: var(--brand-blue);
  }
  .wordmark__name {
    color: var(--text-light); font-weight: 700; text-transform: uppercase;
    letter-spacing: 1px; line-height: 1.05;
  }
  .card--front .wordmark { left: 147px; top: 149px; }
  .card--front .wordmark__square { width: 46px; height: 46px; }
  .card--front .wordmark__name { font-size: 23px; }

  .card--back .wordmark { left: 41px; top: 41px; gap: 12px; }
  .card--back .wordmark__square { width: 40px; height: 40px; }
  .card--back .wordmark__name { font-size: 19px; }

  .contact-person { position: absolute; left: 41px; top: 142px; }
  .contact-person__name { color: var(--brand-blue); font-weight: 700; font-size: 19px; line-height: 1.2; }
  .contact-person__role { color: var(--text-soft); font-size: 15px; line-height: 1.3; }

  .contact-list { position: absolute; left: 41px; top: 218px; list-style: none; }
  .contact-list__item {
    display: flex; align-items: flex-start; gap: 6px;
    color: var(--text-soft); font-size: 15px; line-height: 20px;
  }
  .contact-list__item + .contact-list__item { margin-top: 1px; }
  .contact-list__item--address { margin-bottom: 7px; }
  .contact-list__icon { width: 13px; height: 13px; margin-top: 4px; flex: none; }

  .growth-visual {
    position: absolute; left: 324px; top: 0; width: 286px; height: 320px;
    background: linear-gradient(160deg, rgba(53,162,216,0.55) 0%, rgba(53,162,216,0.18) 60%, rgba(19,33,43,0) 100%);
  }
  .web-band {
    position: absolute; left: 0; bottom: 0; width: 100%; height: 28px;
    background: var(--brand-blue);
    color: var(--text-light); font-weight: 700; font-size: 15px;
    line-height: 28px; padding-left: 41px;
  }
</style>
</head>
<body>
<main class="canvas">
  <section class="card card--front" aria-label="Card front">
    <div class="front-pattern" role="img" aria-label="Repeated brand symbol pattern fading from light to dark"></div>
    <div class="wordmark">
      <span class="wordmark__square" aria-hidden="true"></span>
      <span class="wordmark__name">Halvenmoor<br>Financial Consulting</span>
    </div>
  </section>

  <section class="card card--back" aria-label="Card back">
    <div class="growth-visual" role="img" aria-label="Large rising bar graphic in brand blue"></div>
    <div class="wordmark">
      <span class="wordmark__square" aria-hidden="true"></span>
      <span class="wordmark__name">Halvenmoor<br>Financial Consulting</span>
    </div>

    <div class="contact-person">
      <p class="contact-person__name">Daniel Whitford</p>
      <p class="contact-person__role">President</p>
    </div>

    <ul class="contact-list">
      <li class="contact-list__item contact-list__item--address">
        <svg class="contact-list__icon" viewBox="0 0 14 14" aria-hidden="true"><path d="M7 1.2a4 4 0 0 0-4 4c0 3 4 7.6 4 7.6s4-4.6 4-7.6a4 4 0 0 0-4-4z" fill="none" stroke="#35a2d8" stroke-width="1.3"/><circle cx="7" cy="5.2" r="1.4" fill="none" stroke="#35a2d8" stroke-width="1.2"/></svg>
        <span>415 Linden Park Way, Suite 210<br>Fairbrook, CA 95021</span>
      </li>
      <li class="contact-list__item">
        <svg class="contact-list__icon" viewBox="0 0 14 14" aria-hidden="true"><path d="M3 1.5l2 .3 1 2.6-1.3 1.2a8 8 0 0 0 3.7 3.7L9.6 8l2.6 1 .3 2-1.4 1.4C6.6 12.4 1.6 7.4 1.6 2.9z" fill="none" stroke="#35a2d8" stroke-width="1.2" stroke-linejoin="round"/></svg>
        <span>555-210-4389</span>
      </li>
      <li class="contact-list__item">
        <svg class="contact-list__icon" viewBox="0 0 14 14" aria-hidden="true"><rect x="1" y="2.5" width="12" height="9" fill="none" stroke="#35a2d8" stroke-width="1.2"/><path d="M1 3l6 4.5L13 3" fill="none" stroke="#35a2d8" stroke-width="1.2"/></svg>
        <span>daniel@halvenmoor.com</span>
      </li>
    </ul>

    <div class="web-band">www.halvenmoor.com</div>
  </section>
</main>
</body>
</html>
```